Korvath Supply Website Redesign

Currently korvathsupply.example is focussed on fulfillment and transport from various products in the BBQ segment. However, no we want to update our business activities to Product Development, Brand Development, Online Positioning, Logistics & Aftersales, and Promotional BBQs. We will be a business for Outdoor Leisure Development from A to Z.

Therefore, we need a brand new website. The colours of the current website may be the same. However, i'd like to keep it clean. More white and use blue and green as accent colours. It is a business to business organization so the website should be looking formal and corporate. However we sell fun products so not too formal and corporate.

Pages we need; Home, About, Contact, Our Services (+ page per service) a place to share our news/blogs.

I have added some sort of mock up of an idea. However it needs some finetuning.

Target Market(s)

Businesses

Industry/Entity Type

Corporate/Logistics/Marketing

Coding

Coded - Design and coding required

Colors

Designer to choose colors to be used in the design.

Requirements
Must have
• Show clear distinguishing of the different services we provide (Product Development, Brand Development, Online Positioning, Logistics & Aftersales and Promotional BBQs). Every service should have its own page too. Besides, I would like to have a blog page to share relevant content.
Nice to have
• Show that we are the expert in Outdoor LEisure Development from A to Z
Should not have
• Be too informal. It may be semi-formal

```html
<!DOCTYPE html>
<html lang="en">
<head>
<meta charset="utf-8">
<title>Korvath Supply – Outdoor Leisure Development</title>
<link rel="stylesheet" href="https://fonts.googleapis.com/css2?family=Montserrat:wght@700;800&family=Work+Sans:wght@400;500;600;700&display=swap">
<style>
:root{
  --green:#2f9e3b;
  --teal:#35606f;
  --ink:#1c1c1e;
  --dark:#18191b;
  --white:#ffffff;
}
*{box-sizing:border-box;margin:0;padding:0}
html,body{width:671px;height:1200px;overflow:hidden;background:var(--white)}
body{position:relative;font-family:"Work Sans",sans-serif;color:var(--ink)}
.topline{position:absolute;top:0;left:0;width:671px;height:2px;background:var(--green)}
.site-header{position:absolute;top:2px;left:0;width:671px;height:46px}
.brand{position:absolute;left:62px;top:11px;display:flex;align-items:center;gap:6px}
.brand-dot{width:18px;height:18px;border-radius:50%;background:var(--green)}
.brand-name{font-family:"Montserrat",sans-serif;font-weight:800;font-size:17px;color:var(--teal);letter-spacing:-.2px}
.main-nav{position:absolute;left:231px;top:18px;display:flex;gap:16px;font-weight:700;font-size:8.4px;letter-spacing:.2px}
.main-nav a{color:var(--ink);text-decoration:none}
.main-nav a.active{color:var(--green)}
.social{position:absolute;left:535px;top:14px;display:flex;gap:4px}
.social span{width:21px;height:21px;border-radius:50%;background:#fff;box-shadow:0 1px 3px rgba(0,0,0,.18);display:flex;align-items:center;justify-content:center}
.social span:first-child{background:var(--green)}
.hero{position:absolute;top:48px;left:0;width:671px;height:400px}
.hero-title{position:absolute;top:197px;left:0;width:671px;text-align:center;font-family:"Montserrat",sans-serif;font-weight:800;font-size:21px;line-height:27px;color:#fff;text-shadow:0 1px 4px rgba(0,0,0,.35)}
.services{position:absolute;top:366px;left:62px;display:flex;gap:10.5px}
.service-card{position:relative;width:101px;height:109px;background:#fff;border-radius:4px;box-shadow:0 2px 8px rgba(0,0,0,.12);text-align:center}
.service-card .icon{position:absolute;top:13px;left:50%;margin-left:-15px;width:30px;height:30px}
.service-card h3{position:absolute;top:54px;left:0;width:100%;font-weight:700;font-size:8.4px;line-height:15px;color:var(--teal);letter-spacing:.3px}
.service-card.featured{background:var(--teal)}
.service-card.featured h3{top:11px;color:#fff}
.service-card.featured p{position:absolute;top:46px;left:5px;right:5px;font-size:6.8px;line-height:12px;color:#fff;font-weight:500}
.go{position:absolute;left:50%;margin-left:-10px;bottom:-10px;width:20px;height:20px;border-radius:50%;background:var(--green);display:flex;align-items:center;justify-content:center}
.difference{position:absolute;top:539px;left:0;width:671px;height:192px;background:linear-gradient(110deg,#1d3340 0%,#131b22 45%,#0e1215 70%,#122417 100%);text-align:center;color:#fff}
.difference h2{position:absolute;top:43px;width:100%;font-family:"Montserrat",sans-serif;font-weight:800;font-size:19px;letter-spacing:.2px}
.difference .rule{position:absolute;top:75px;left:277px;width:118px;height:1px;background:#fff}
.difference p{position:absolute;top:99px;left:76px;width:519px;font-size:7.8px;line-height:15px;font-weight:600}
.news-title{position:absolute;top:778px;width:671px;text-align:center;font-family:"Montserrat",sans-serif;font-weight:800;font-size:21px;color:var(--ink)}
.news-rule{position:absolute;top:809px;left:298px;width:75px;height:1.5px;background:var(--green)}
.news{position:absolute;top:839px;left:62px;display:flex;gap:15px}
.news-card{position:relative;width:172px;height:134px;border-radius:4px;overflow:hidden;color:#fff}
.news-card .photo{position:absolute;inset:0}
.news-card .shade{position:absolute;inset:0;background:linear-gradient(180deg,rgba(0,0,0,0) 40%,rgba(0,0,0,.6) 100%)}
.news-card.active .shade{background:rgba(20,26,30,.72)}
.news-card h4{position:absolute;left:11px;right:8px;top:83px;font-weight:500;font-size:9px;line-height:13px;letter-spacing:.4px}
.news-card time{position:absolute;left:11px;top:114px;font-size:7.4px;font-weight:500}
.news-card.active h4{top:47px}
.news-card.active time{top:80px}
.read-more{position:absolute;left:14px;top:116px;font-size:7.4px;font-weight:700;color:var(--green);display:flex;align-items:center;gap:4px}
.site-footer{position:absolute;top:1024px;left:0;width:671px;height:176px}
.footer-brand{position:absolute;top:1075px;left:0;width:671px;display:flex;justify-content:center;align-items:center;gap:8px}
.footer-brand .brand-dot{width:20px;height:20px}
.footer-brand .brand-name{color:#fff;font-size:21px}
.footer-nav{position:absolute;top:1121px;left:0;width:671px;display:flex;justify-content:center;gap:23px;font-weight:600;font-size:10.4px;letter-spacing:.3px}
.footer-nav a{color:#fff;text-decoration:none}
.address{position:absolute;top:1143px;left:0;width:671px;color:#fff;font-size:8px;font-weight:500;letter-spacing:.2px;display:flex;justify-content:center;gap:6px;align-items:center}
.footer-rule{position:absolute;top:1170px;left:62px;width:547px;height:1px;background:#3b3d40}
.copyright{position:absolute;top:1180px;left:0;width:671px;text-align:center;color:#fff;font-size:7.6px}
.copyright b{font-weight:700}
</style>
</head>
<body>
<div class="topline"></div>

<header class="site-header">
  <div class="brand"><span class="brand-dot"></span><span class="brand-name">Korvath Supply</span></div>
  <nav class="main-nav">
    <a class="active" href="#">HOME</a><a href="#">ABOUT</a><a href="#">OUR SERVICES</a><a href="#">BLOGS</a><a href="#">CONTACT</a>
  </nav>
  <div class="social">
    <span><svg width="8" height="8" viewBox="0 0 8 8"><circle cx="4" cy="4" r="2" fill="#fff"/></svg></span>
    <span><svg width="8" height="8" viewBox="0 0 8 8"><circle cx="4" cy="4" r="2" fill="var(--green)"/></svg></span>
    <span><svg width="8" height="8" viewBox="0 0 8 8"><circle cx="4" cy="4" r="2" fill="var(--green)"/></svg></span>
  </div>
</header>

<section class="hero">
  <svg width="671" height="400" viewBox="0 0 671 400">
    <defs>
      <linearGradient id="heroSky" x1="0" y1="0" x2="0" y2="1">
        <stop offset="0" stop-color="#3e4a5c"/>
        <stop offset="0.25" stop-color="#c0703a"/>
        <stop offset="0.45" stop-color="#7c5a48"/>
        <stop offset="0.7" stop-color="#4a3c3a"/>
        <stop offset="1" stop-color="#2a3036"/>
      </linearGradient>
    </defs>
    <path d="M0 0H671V300Q335 472 0 300Z" fill="var(--green)"/>
    <path role="img" aria-label="Aerial photo of a container port and cargo ship at sunset" d="M0 0H671V295Q335 462 0 295Z" fill="url(#heroSky)"/>
  </svg>
  <h1 class="hero-title">OUTDOOR LEISURE<br>DEVELOPMENT FROM A TO Z</h1>
</section>

<section class="services">
  <article class="service-card">
    <svg class="icon" viewBox="0 0 30 30"><circle cx="15" cy="15" r="12" fill="none" stroke="var(--green)" stroke-width="4" stroke-dasharray="4 2.3"/><circle cx="15" cy="15" r="9" fill="var(--green)"/><path d="M10 12l5-2.5 5 2.5v6l-5 2.5-5-2.5z" fill="none" stroke="#fff" stroke-width="1.3"/><path d="M10 12l5 2.5 5-2.5M15 14.5v6" stroke="#fff" stroke-width="1.3" fill="none"/></svg>
    <h3>PRODUCT<br>DEVELOPMENT</h3>
    <span class="go"><svg width="8" height="8" viewBox="0 0 8 8"><path d="M3 1.5L5.5 4 3 6.5" stroke="#fff" stroke-width="1.3" fill="none"/></svg></span>
  </article>
  <article class="service-card">
    <svg class="icon" viewBox="0 0 30 30"><circle cx="12" cy="10" r="6.5" fill="var(--green)"/><rect x="9.5" y="16" width="5" height="5" fill="var(--green)"/><path d="M12 21v4h4" stroke="var(--green)" stroke-width="1.3" fill="none"/><path d="M18 18l4-4 4 4v10h-8z" fill="var(--green)"/><path d="M12 1v2M4 4l1.5 1.5M20 4l-1.5 1.5" stroke="var(--green)" stroke-width="1.3"/></svg>
    <h3>BRAND<br>DEVELOPMENT</h3>
    <span class="go"><svg width="8" height="8" viewBox="0 0 8 8"><path d="M3 1.5L5.5 4 3 6.5" stroke="#fff" stroke-width="1.3" fill="none"/></svg></span>
  </article>
  <article class="service-card featured">
    <h3>ONLINE<br>POSITIONING</h3>
    <p>Es un hecho establecido hace demasiado tiempo que un lector se distraerá</p>
    <span class="go"><svg width="8" height="8" viewBox="0 0 8 8"><path d="M3 1.5L5.5 4 3 6.5" stroke="#fff" stroke-width="1.3" fill="none"/></svg></span>
  </article>
  <article class="service-card">
    <svg class="icon" viewBox="0 0 30 30"><circle cx="15" cy="15" r="9" fill="none" stroke="var(--green)" stroke-width="1.8"/><ellipse cx="15" cy="15" rx="4" ry="9" fill="none" stroke="var(--green)" stroke-width="1.5"/><path d="M6 15h18" stroke="var(--green)" stroke-width="1.5"/><circle cx="15" cy="3" r="2.3" fill="var(--green)"/><circle cx="15" cy="27" r="2.3" fill="var(--green)"/><circle cx="3" cy="15" r="2.3" fill="var(--green)"/><circle cx="27" cy="15" r="2.3" fill="var(--green)"/></svg>
    <h3>LOGISTICS<br>&amp; AFTERSALES</h3>
    <span class="go"><svg width="8" height="8" viewBox="0 0 8 8"><path d="M3 1.5L5.5 4 3 6.5" stroke="#fff" stroke-width="1.3" fill="none"/></svg></span>
  </article>
  <article class="service-card">
    <svg class="icon" viewBox="0 0 30 30"><path d="M4 12h22a11 11 0 0 1-22 0z" fill="var(--green)"/><path d="M3 10h24" stroke="var(--green)" stroke-width="2"/><path d="M10 22l-3 7M20 22l3 7M15 23v6" stroke="var(--green)" stroke-width="1.8"/><path d="M11 2q2 2 0 4M15 1q2 2 0 4M19 2q2 2 0 4" stroke="var(--green)" stroke-width="1.3" fill="none"/></svg>
    <h3>PROMOTIONAL<br>BBQS</h3>
    <span class="go"><svg width="8" height="8" viewBox="0 0 8 8"><path d="M3 1.5L5.5 4 3 6.5" stroke="#fff" stroke-width="1.3" fill="none"/></svg></span>
  </article>
</section>

<section class="difference" role="img" aria-label="Dark background photo of a hand touching a digital gear interface with green diagonal stripes">
  <h2>WE MAKE THE DIFFERENCE</h2>
  <div class="rule"></div>
  <p>Sed ut perspiciatis unde omnis iste natus error sit voluptatem accusantium doloremque laudantium, totam rem aperiam, eaque ipsa quae ab illo inventore veritatis et quasi architecto beatae vitae dicta sunt explicabo. Nemo enim ipsam voluptatem quia voluptas sit aspernatur aut odit aut fugitea.</p>
</section>

<h2 class="news-title">LATEST NEWS</h2>
<div class="news-rule"></div>
<section class="news">
  <article class="news-card">
    <div class="photo" role="img" aria-label="Photo of two businessmen talking in an office" style="background:linear-gradient(135deg,#8797a6 0%,#4a5b6c 50%,#2b3a52 100%)"></div>
    <div class="shade"></div>
    <h4>LOREM IPSUM DOLOR SIT AIE CONSEUR ADIPISEA.</h4>
    <time>15 DEC 2021</time>
  </article>
  <article class="news-card active">
    <div class="photo" role="img" aria-label="Photo of hands typing on a laptop with digital icons" style="background:linear-gradient(135deg,#7a6a52 0%,#4e5a58 50%,#2c3a3e 100%)"></div>
    <div class="shade"></div>
    <h4>LOREM IPSUM DOLOR SIT AIE CONSEUR ADIPISEA.</h4>
    <time>15 DEC 2021</time>
    <span class="read-more">READ MORE <svg width="7" height="7" viewBox="0 0 8 8"><circle cx="4" cy="4" r="4" fill="var(--green)"/><path d="M3 2l2 2-2 2" stroke="#1c2226" stroke-width="1.2" fill="none"/></svg></span>
  </article>
  <article class="news-card">
    <div class="photo" role="img" aria-label="Aerial photo of a container terminal at sunset" style="background:linear-gradient(180deg,#c78a5a 0%,#8a6a5a 35%,#4c4a52 70%,#3a3240 100%)"></div>
    <div class="shade"></div>
    <h4>LOREM IPSUM DOLOR SIT AIE CONSEUR ADIPISEA.</h4>
    <time>15 DEC 2021</time>
  </article>
</section>

<footer>
  <svg class="site-footer" width="671" height="176" viewBox="0 0 671 176">
    <path d="M0 90Q335 -80 671 90V176H0Z" fill="var(--green)"/>
    <path d="M0 95Q335 -72 671 95V176H0Z" fill="var(--dark)"/>
  </svg>
  <div class="footer-brand"><span class="brand-dot"></span><span class="brand-name">Korvath Supply</span></div>
  <nav class="footer-nav"><a href="#">HOME</a><a href="#">ABOUT</a><a href="#">OUR SERVICES</a><a href="#">BLOGS</a><a href="#">CONTACT</a></nav>
  <p class="address"><svg width="6" height="8" viewBox="0 0 6 8"><path d="M3 0a3 3 0 0 1 3 3c0 2-3 5-3 5S0 5 0 3a3 3 0 0 1 3-3z" fill="var(--green)"/><circle cx="3" cy="3" r="1" fill="var(--dark)"/></svg>Lindenhof Kade 212, 4810 KL Veldhaven</p>
  <div class="footer-rule"></div>
  <p class="copyright">© 2021 <b>Korvath Supply</b>. All Rights Reserved</p>
</footer>
</body>
</html>
```